The Harbourlight Dental centre, the Zorvik of dentistry

New concept of running a dental practice by having a walk in practice
WE ARE A HUSBAND AND WIFE TEAM

Really modern and sophisticated, we want it to feel different from the traditional dental practice.
we want it split into different pages:CONTACT US
LOCATION: Information about our location since patients often confuse us with the practice across the road
ABOUT US:
Opening hours - & 7 Days, We offer a weekend service
WALK IN: We offer a walk in service for dental treatments
TREATMENTS we offer

DENTAL ADVICE: Free dentist advise call back- So a dentist will call you back for free to discuss

Target Market(s)

Everyone

Industry/Entity Type

Dental

Coding

Coded - Design and coding required

Number of Pages Required

5+ page

Requirements
Must have
• First page
• * changing pictures
• *opening times
• * our walk in concept I.e. no appointment needed
• *logo
• * links in to clinic tidal (online booking system in Australia)
• * address /phone number/email
• * possible videos
• Second page
• meet the team
• third page
• dental treatments/walk in treatments
• fourth page
• dental advice with vid larko videos
• Fifth page
• contact us/maps/ we get confused with the dental practice across the road
• We would also like a giving back page. In this please include the photo's below of our dental mission in Guatemala, where by we did treatment for patients as part of a charity.
Nice to have
• Changing pictures on the home screen
• videos linked to home page

```html
<!DOCTYPE html>
<html lang="en">
<head>
<meta charset="utf-8">
<title>The Harbourlight Dental centre – Dental Treatments</title>
<link href="https://fonts.googleapis.com/css2?family=Open+Sans:wght@400;600&display=swap" rel="stylesheet">
<style>
:root{
  --green:#9cc43c;
  --blue:#1ba1e2;
  --ink:#555;
  --ink-dark:#333;
  --rule:#d9d9d9;
  --band:#f2f2f2;
  --footer:#3b3b3b;
  --footer-text:#cfcfcf;
}
*{margin:0;padding:0;box-sizing:border-box}
html,body{width:733px;height:1200px;overflow:hidden;background:#fff;font-family:"Open Sans",Arial,sans-serif;color:var(--ink)}
.page{position:relative;width:733px;height:1200px}
.topbar{position:absolute;top:0;left:0;width:733px;height:3px;background:linear-gradient(90deg,var(--green) 50%,var(--blue) 50%)}
.brand{position:absolute;left:81px;top:20px;display:flex;align-items:center;gap:8px}
.brand-mark{width:30px;height:30px;border-radius:50%;background:var(--blue)}
.brand-name{font-size:15px;font-weight:600;color:var(--green);line-height:1.1}
.header-info{position:absolute;right:82px;top:29px;text-align:right;font-size:6px;color:#777}
.header-info span{margin-left:8px}
.header-contact{position:absolute;right:82px;top:41px;font-size:10px;color:var(--blue);display:flex;gap:12px}
.header-contact span{display:flex;align-items:center;gap:4px}
.nav{position:absolute;left:81px;top:77px;width:570px;height:32px;background:var(--green);display:flex}
.nav a{color:#fff;text-decoration:none;font-size:7px;text-transform:uppercase;display:flex;align-items:center;justify-content:center;height:100%}
.nav a.active{background:var(--blue)}
.nav-shadow{position:absolute;left:0;top:109px;width:733px;height:4px;background:#ececec}
.treatment-open{position:absolute;left:81px;top:133px;width:570px}
.acc-title{display:flex;align-items:center;gap:8px;font-size:20px;color:#666}
.acc-title.open{color:var(--green)}
.acc-icon{width:11px;height:11px;flex:none}
.open-body{display:flex;gap:12px;margin-top:11px}
.photo{background:linear-gradient(135deg,#3b6fa5,#c7d7e3 55%,#8e3340)}
.open-photo{width:149px;height:117px}
.open-text{font-size:6.3px;line-height:1.8;color:#666;padding-top:0}
.open-text p{margin-bottom:8px}
.open-text strong{font-weight:400;font-size:7.5px;color:#333}
.open-rule{position:absolute;left:81px;top:301px;width:570px;height:1px;background:var(--green)}
.accordion{position:absolute;left:81px;top:302px;width:570px;list-style:none}
.accordion li{height:58.6px;border-bottom:1px solid var(--rule);display:flex;align-items:center}
.gallery{position:absolute;left:0;top:750px;width:733px;height:211px;background:var(--band)}
.gallery h2{position:absolute;top:17px;width:100%;text-align:center;font-size:19px;font-weight:400;color:var(--green)}
.gallery-photo{position:absolute;top:52px;width:134px;height:112px}
.dots{position:absolute;top:181px;left:0;width:100%;display:flex;justify-content:center;gap:8px}
.dots i{width:6px;height:6px;border-radius:50%;background:#bbb}
.dots i.on{background:var(--green)}
.map{position:absolute;left:0;top:961px;width:366px;height:150px;background:linear-gradient(160deg,#e4e4e4,#c9c9c9)}
.contact{position:absolute;left:366px;top:961px;width:367px;height:150px;background:#ebebeb}
.contact h2{position:absolute;left:30px;top:16px;font-size:15px;font-weight:400;color:var(--ink-dark)}
.field{position:absolute;width:111px;height:22px;background:#fff;font-size:7px;color:#666;padding-left:10px;display:flex;align-items:center}
.submit{position:absolute;width:111px;height:22px;background:var(--ink-dark);color:#fff;font-size:7px;display:flex;align-items:center;justify-content:center}
.footer{position:absolute;left:0;top:1111px;width:733px;height:89px;background:var(--footer);color:var(--footer-text)}
.footer-info{position:absolute;top:14px;left:81px;width:570px;display:flex;font-size:6.5px;align-items:center}
.footer-info span{display:flex;align-items:center;gap:6px}
.socials{margin-left:auto;display:flex;gap:9px}
.socials i{width:6px;height:6px;border-radius:50%;background:#777}
.footer-rule{position:absolute;left:81px;top:38px;width:570px;height:1px;background:#555}
.footer-links{position:absolute;left:81px;top:51px;font-size:5.5px}
.copyright{position:absolute;left:81px;top:66px;font-size:5.5px}
.booking{position:absolute;right:82px;top:52px;display:flex;align-items:center;gap:8px;font-size:5.5px}
.booking-name{font-size:12px;color:#aaa}
</style>
</head>
<body>
<div class="page">
  <div class="topbar"></div>

  <div class="brand">
    <div class="brand-mark"></div>
    <div class="brand-name">The Harbourlight<br>Dental centre</div>
  </div>

  <div class="header-info">
    <span>&#9679; Unit 7, 18 Kestrel Parade, Wanbury, WA 6071</span>
    <span>&#9719; OPEN 8 AM TO 8PM 7 DAYS A WEEK</span>
  </div>
  <div class="header-contact">
    <span><svg width="8" height="8" viewBox="0 0 10 10"><path d="M2 1l2 2-1 1.5c.7 1.3 1.7 2.3 3 3L7.5 6l2 2-1.5 1.5C4.5 9 1 5.5.5 2z" fill="currentColor"/></svg>08 5550 1427</span>
    <span><svg width="10" height="8" viewBox="0 0 10 8"><rect width="10" height="8" fill="currentColor"/><path d="M0 0l5 4 5-4" stroke="#fff" fill="none"/></svg>info@harbourlightdental.example</span>
  </div>

  <nav class="nav">
    <a style="width:70px">Home</a>
    <a style="width:79px">Meet the Team</a>
    <a class="active" style="width:211px">Dental Treatments/Walk-in Treatments</a>
    <a style="width:96px">Dental Advice</a>
    <a style="width:114px">Contact Us</a>
  </nav>
  <div class="nav-shadow"></div>

  <section class="treatment-open">
    <h2 class="acc-title open">
      <svg class="acc-icon" viewBox="0 0 11 11"><rect x=".5" y=".5" width="10" height="10" rx="2" fill="none" stroke="currentColor"/><path d="M3 5.5h5" stroke="currentColor"/></svg>
      <span style="font-weight:400">Extractions</span>
    </h2>
    <div class="open-body">
      <div class="photo open-photo" role="img" aria-label="Dentist performing a tooth extraction on a patient"></div>
      <div class="open-text">
        <p>We will always try to save a healthy tooth. However sometimes it does become necessary to take a tooth out. For instance when a tooth has a very large hole in that cannot be fixed by your dentist.</p>
        <p>This procedure is typically very quick. <strong>We will ensure you have the most comfortable experience possible.</strong> It is important to share with your doctor any worries you may have.</p>
      </div>
    </div>
  </section>
  <div class="open-rule"></div>

  <ul class="accordion">
    <li><h2 class="acc-title"><svg class="acc-icon" viewBox="0 0 11 11"><rect x=".5" y=".5" width="10" height="10" rx="2" fill="none" stroke="currentColor"/><path d="M3 5.5h5M5.5 3v5" stroke="currentColor"/></svg><span style="font-weight:400">Dentures</span></h2></li>
    <li><h2 class="acc-title"><svg class="acc-icon" viewBox="0 0 11 11"><rect x=".5" y=".5" width="10" height="10" rx="2" fill="none" stroke="currentColor"/><path d="M3 5.5h5M5.5 3v5" stroke="currentColor"/></svg><span style="font-weight:400">Fillings</span></h2></li>
    <li><h2 class="acc-title"><svg class="acc-icon" viewBox="0 0 11 11"><rect x=".5" y=".5" width="10" height="10" rx="2" fill="none" stroke="currentColor"/><path d="M3 5.5h5M5.5 3v5" stroke="currentColor"/></svg><span style="font-weight:400">Root Canal Treatment</span></h2></li>
    <li><h2 class="acc-title"><svg class="acc-icon" viewBox="0 0 11 11"><rect x=".5" y=".5" width="10" height="10" rx="2" fill="none" stroke="currentColor"/><path d="M3 5.5h5M5.5 3v5" stroke="currentColor"/></svg><span style="font-weight:400">Periodontal Treatment</span></h2></li>
    <li><h2 class="acc-title"><svg class="acc-icon" viewBox="0 0 11 11"><rect x=".5" y=".5" width="10" height="10" rx="2" fill="none" stroke="currentColor"/><path d="M3 5.5h5M5.5 3v5" stroke="currentColor"/></svg><span style="font-weight:400">Crowns and Bridges</span></h2></li>
    <li><h2 class="acc-title"><svg class="acc-icon" viewBox="0 0 11 11"><rect x=".5" y=".5" width="10" height="10" rx="2" fill="none" stroke="currentColor"/><path d="M3 5.5h5M5.5 3v5" stroke="currentColor"/></svg><span style="font-weight:400">Teeth Whitening</span></h2></li>
    <li><h2 class="acc-title"><svg class="acc-icon" viewBox="0 0 11 11"><rect x=".5" y=".5" width="10" height="10" rx="2" fill="none" stroke="currentColor"/><path d="M3 5.5h5M5.5 3v5" stroke="currentColor"/></svg><span style="font-weight:400">Facial Aesthetics</span></h2></li>
  </ul>

  <section class="gallery">
    <h2>Gallery</h2>
    <div class="gallery-photo" style="left:81px;background:linear-gradient(180deg,#6f6a63,#c9c3bc 40%,#4a6aa0)" role="img" aria-label="Group photo of the dental mission team"></div>
    <div class="gallery-photo" style="left:226px;background:linear-gradient(180deg,#8a5a35,#d8cdbf 45%,#6b7aa0)" role="img" aria-label="Hall set up as a temporary dental clinic"></div>
    <div class="gallery-photo" style="left:372px;background:linear-gradient(180deg,#8da0b8,#c49c8a 50%,#3a3a3a)" role="img" aria-label="Town street scene during the mission"></div>
    <div class="gallery-photo" style="left:518px;background:linear-gradient(180deg,#d9d9d9,#7a7a7a 50%,#4a5a3a)" role="img" aria-label="Volunteers treating a child patient"></div>
    <div class="dots"><i class="on"></i><i></i><i></i><i></i></div>
  </section>

  <div class="map" role="img" aria-label="World map showing the clinic location"></div>
  <section class="contact">
    <h2>Contact Us</h2>
    <div class="field" style="left:31px;top:42px">First Name</div>
    <div class="field" style="left:148px;top:42px">Last Name</div>
    <div class="field" style="left:31px;top:71px">Phone</div>
    <div class="field" style="left:148px;top:71px">Email</div>
    <div class="field" style="left:31px;top:101px">City</div>
    <div class="submit" style="left:148px;top:101px">SUBMIT</div>
  </section>

  <footer class="footer">
    <div class="footer-info">
      <span style="width:216px"><svg width="6" height="8" viewBox="0 0 6 8"><path d="M3 0a3 3 0 013 3c0 2-3 5-3 5S0 5 0 3a3 3 0 013-3z" fill="currentColor"/></svg>Unit 7, 18 Kestrel Parade, Wanbury, WA 6071</span>
      <span style="width:115px"><svg width="8" height="8" viewBox="0 0 10 10"><path d="M2 1l2 2-1 1.5c.7 1.3 1.7 2.3 3 3L7.5 6l2 2-1.5 1.5C4.5 9 1 5.5.5 2z" fill="currentColor"/></svg>Call Now: 08 5550 1427</span>
      <span><svg width="9" height="7" viewBox="0 0 10 8"><rect width="10" height="8" fill="currentColor"/><path d="M0 0l5 4 5-4" stroke="#3b3b3b" fill="none"/></svg>Email: info@harbourlightdental.example</span>
      <div class="socials"><i></i><i></i><i></i><i></i></div>
    </div>
    <div class="footer-rule"></div>
    <div class="footer-links">Home &nbsp;|&nbsp; Meet the Team &nbsp;|&nbsp; Dental Treatments/Walk-in Treatments &nbsp;|&nbsp; Dental Advice &nbsp;|&nbsp; Contact us</div>
    <div class="copyright">Copyright © 2016 The Harbourlight Dental centre. &nbsp;All rights reserved.</div>
    <div class="booking"><span>Appointment Booking</span><span class="booking-name">clinic tidal</span></div>
  </footer>
</div>
</body>
</html>
```